Ashmoor DAYS: Final product due on March 4, 2019

We need a newspaper ad for a retirement community called "Tal Roon" located in Manteca, CA. We are estate planning law firm. We would like to include our logo (either blue or white background one) and contents attached (we are flexible to reduce a number of characters), as well as our photo (w/ white background) that will be sent later. We would like to see designs that draw attentions from senior people. You are free to be creative!
Size: 10” wide x 5.5” high
Specs: Artwork must be provided electronically in a pdf format. Color ads must be provided in a color format.

Target Market(s)

Active retirement community in Manteca, CA

Industry/Entity Type

Law Firm

Colors

Designer to choose colors to be used in the design.

Requirements
Must have
• Our logo and contents - see attachments.
• Our photo to be sent tomorrow.
Nice to have
• Use good colors for newspaper ad.
• You are free to be creative.

```html
<!DOCTYPE html>
<html lang="en">
<head>
<meta charset="utf-8">
<title>Forward Estate Counsel – Newspaper Ad</title>
<link rel="stylesheet" href="https://fonts.googleapis.com/css2?family=Montserrat:wght@500&family=Open+Sans:wght@300;400;600;700;800&display=swap">
<style>
  :root {
    --navy: #0f1f5c;
    --gold: #b8862d;
    --white: #ffffff;
    --ink: #1a1a1a;
    --quote-bg: #ececec;
    --photo-dark: #3a3631;
    --photo-light: #cfc6b8;
  }
  * { box-sizing: border-box; margin: 0; padding: 0; }
  html, body { width: 1200px; height: 720px; overflow: hidden; background: var(--white); }
  .ad { position: relative; width: 1200px; height: 720px; overflow: hidden; background: var(--white); font-family: "Open Sans", Arial, sans-serif; }
  .shapes { position: absolute; inset: 0; }
  .brand {
    position: absolute; left: 63px; top: 72px; width: 526px; text-align: center;
    font-family: "Montserrat", Arial, sans-serif; font-weight: 500; font-size: 30px;
    letter-spacing: 1px; color: var(--gold); text-transform: uppercase; line-height: 40px;
    white-space: nowrap;
  }
  .headline {
    position: absolute; left: 62px; top: 181px; width: 560px;
    color: var(--white); font-size: 39px; font-weight: 300; line-height: 51px;
    white-space: nowrap;
  }
  .headline strong { font-weight: 800; }
  .bio {
    position: absolute; left: 62px; top: 369px; width: 410px;
    font-size: 12.6px; line-height: 19.6px; color: var(--ink);
  }
  .address {
    position: absolute; left: 118px; top: 581px; color: var(--white);
    font-weight: 300;
  }
  .address .street { font-size: 19px; line-height: 30px; padding-left: 25px; position: relative; }
  .address .pin { position: absolute; left: 0; top: 4px; }
  .address .note { font-size: 14px; line-height: 22px; margin-top: 6px; }
  .testimonial {
    position: absolute; left: 486px; top: 371px; width: 308px; height: 308px;
    border-radius: 50%; background: var(--quote-bg); border: 4px solid var(--white);
    text-align: center; color: var(--ink); padding-top: 26px;
  }
  .testimonial .mark { font-weight: 800; font-size: 64px; line-height: 64px; height: 40px; overflow: hidden; color: var(--ink); }
  .testimonial blockquote { font-size: 15px; line-height: 23px; margin-top: 8px; }
  .testimonial cite { display: block; font-style: normal; font-weight: 700; font-size: 15px; line-height: 20px; margin-top: 8px; }
  .testimonial .mark.close { margin-top: 10px; }
  .phone {
    position: absolute; left: 799px; top: 582px; width: 342px; height: 66px;
    border-radius: 33px; background: var(--navy); border: 3px solid var(--white);
    display: flex; align-items: center; gap: 12px; padding-left: 22px;
    color: var(--white); font-weight: 700; font-size: 35px;
  }
  .web {
    position: absolute; left: 800px; top: 660px; color: var(--white);
    font-size: 19px; font-weight: 400; display: flex; align-items: center; gap: 8px;
  }
  .web b { font-weight: 700; }
</style>
</head>
<body>
<div class="ad">
  <svg class="shapes" width="1200" height="720" viewBox="0 0 1200 720">
    <defs>
      <radialGradient id="photoTone" cx="45%" cy="45%" r="70%">
        <stop offset="0" stop-color="var(--photo-light)"/>
        <stop offset="1" stop-color="var(--photo-dark)"/>
      </radialGradient>
    </defs>
    <rect class="headline-band" x="0" y="166" width="720" height="186" fill="var(--navy)"/>
    <path class="gold-wave" d="M0,720 L0,608 C120,545 230,515 330,522 C430,530 520,580 600,620 L760,625 C900,600 1070,535 1200,462 L1200,720 Z" fill="var(--gold)"/>
    <path class="address-hump" d="M0,720 L0,676 C90,560 200,528 270,528 C360,528 470,590 540,720 Z" fill="var(--navy)"/>
    <path class="quote-arc" d="M573,668 A158,158 0 1 1 783,592" fill="none" stroke="var(--navy)" stroke-width="1.5"/>
    <circle class="photo-frame" cx="907" cy="224" r="292" fill="var(--white)"/>
    <circle role="img" aria-label="Photo: attorney pointing a pen at a document on a desk with scales of justice and a gavel, client's hands folded across the table" cx="907" cy="224" r="281" fill="url(#photoTone)"/>
  </svg>

  <div class="brand">Forward Estate Counsel</div>

  <h1 class="headline">Taking care of <strong>your family,</strong><br><strong>finances,</strong> and <strong>healthcare</strong><br>is so vitally <strong>important.</strong></h1>

  <p class="bio">MARTIN ELLERY, a Widely Trusted and Experienced Estate Planning Lawyer, has helped hundreds of Manteca area residents protect themselves and their families. He has a 10/10 score on Counselrank, have been selected as a “Rising Star” by Premier Counsel, and have been selected as one of the Top 20 Estate Planning Attorneys in Sacramento by Bestpick.com. " We want to emphasize "MARTIN ELLERY", "Widely Trusted" and “Estate Planning Laywer".</p>

  <div class="address">
    <div class="street">
      <svg class="pin" width="16" height="22" viewBox="0 0 16 22"><path d="M8 1a6 6 0 0 1 6 6c0 4-6 10-6 10S2 11 2 7a6 6 0 0 1 6-6z" fill="none" stroke="var(--white)" stroke-width="1.6"/><circle cx="8" cy="7" r="2" fill="none" stroke="var(--white)" stroke-width="1.4"/><line x1="2" y1="20.5" x2="14" y2="20.5" stroke="var(--white)" stroke-width="1.6"/></svg>
      2280 North Orchard Avenue,<br>Suite #210, Manteca CA 95336
    </div>
    <div class="note">(On the corner of Orchard and Lincoln)<br>ONLY A SEVEN MINUTE DRIVE FROM TAL ROON!</div>
  </div>

  <div class="testimonial">
    <div class="mark">“</div>
    <blockquote>What we like the best is there<br>is never a cost to speak with<br>Martin about our estate plan.<br>We got all our questions<br>answered and had great peace<br>of mind after working with him!</blockquote>
    <cite>Dale &amp; Marion</cite>
    <div class="mark close">”</div>
  </div>

  <div class="phone">
    <svg width="38" height="38" viewBox="0 0 38 38"><circle cx="19" cy="19" r="17" fill="none" stroke="var(--white)" stroke-width="2.5"/><path d="M13 10l4 4-2.5 2.5c1.2 2.8 3.2 4.8 6 6L23 20l4 4-3 3c-7-1-12.5-6.5-14-14z" fill="var(--white)"/></svg>
    (209) 555-0148
  </div>

  <div class="web">
    <svg width="20" height="20" viewBox="0 0 20 20" fill="none" stroke="var(--white)" stroke-width="1.4"><circle cx="10" cy="10" r="8.5"/><ellipse cx="10" cy="10" rx="3.8" ry="8.5"/><line x1="1.5" y1="10" x2="18.5" y2="10"/><line x1="3" y1="5.5" x2="17" y2="5.5"/><line x1="3" y1="14.5" x2="17" y2="14.5"/></svg>
    <span>www.<b>ForwardEstateLaw</b>.com</span>
  </div>
</div>
</body>
</html>
```